South Florida Real Estate Brokerage Business

The name is LAKE VORISSA REAL ESTATE.
The company is a Real estate realty based in Miami.
Is targeted to Latin American clients.
Must express luxury, and efficiency.
Target clients for properties around 250k to a million +.
Vorissa means Royal in Latin.
Should communicate safety and knowledge of the product and transaction with a tech edge.

The web design needs to be a Social tool, with Friendloop and other media integration of some sort. Needs to have a Show case place, a Search place (MLS listings) with maps and filters.
Needs to reflect luxury but also mixed with a social edge capable of engaging clients or transition them to communicate with the page.
Include the logo from the uploaded files, feel free to change the color or font per webdesign.
This is a Front en design, layout and graphics.
Possible future programming if approved.
I can receive Quotes for the Code part.

Spanish and English speakers living in Latin America and Canada looking for apartments and houses to buy.

Business

• Search area.
Neighbourhood area.
Could be a blog or news area.
Client registration.
Social Plugin
• Social linking to networks.
Log in with friendloop account.
Friendloop Like.

```html
<!DOCTYPE html>
<html lang="en">
<head>
<meta charset="utf-8">
<title>Lake Vorissa Real Estate</title>
<link href="https://fonts.googleapis.com/css2?family=Open+Sans:wght@400;600;700&family=PT+Sans+Narrow:wght@400;700&family=Great+Vibes&display=swap" rel="stylesheet">
<style>
:root{
  --bg:#1f1f1f; --white:#fff; --ink:#333; --muted:#888; --gold:#b8892a; --gold-dark:#8a6a1e;
  --red:#c0202a; --blue:#2a5aa0; --loop:#3b5998; --panel:#d6d6d6; --panel-edge:#c4c4c4;
  --cream:#efe8d2; --cream-edge:#d9cfb0; --nav:#8e8e8e; --footer-text:#666;
}
*{box-sizing:border-box;margin:0;padding:0}
html,body{width:681px;height:1200px;overflow:hidden;background:var(--bg)}
body{font-family:"Open Sans",Arial,sans-serif;color:var(--ink);font-size:8px}
.page{position:relative;width:681px;height:1200px}
.abs{position:absolute}
.sheet{left:62px;top:0;width:556px;height:1068px;background:var(--white)}
.header{left:62px;top:0;width:556px;height:80px;background:linear-gradient(#fbf8ef,#f1ead6 80%,#e6dcc0)}
.brand{left:70px;top:8px;display:flex;align-items:center;gap:8px}
.brand-mark{width:28px;height:28px;background:var(--gold)}
.brand-name{font-family:"PT Sans Narrow",sans-serif;font-weight:700;color:#3a3a3a;font-size:15px;line-height:15px;letter-spacing:.5px}
.join{left:482px;top:14px;font-size:9px;color:var(--gold)}
.social{left:531px;top:10px;display:flex;gap:3px}
.social span{width:17px;height:17px;border-radius:3px;display:block}
.nav{left:62px;top:80px;width:556px;height:20px;background:linear-gradient(#b0b0b0,#7a7a7a);display:flex;font-size:7px;color:#222}
.nav a{display:flex;align-items:center;padding:0 9px;border-right:1px solid #9a9a9a;color:#222;text-decoration:none}
.nav a.home{width:26px;justify-content:center}
.nav a.active{background:#555;color:#fff;font-weight:600}
.hero{left:62px;top:100px;width:556px;height:233px;background:linear-gradient(180deg,#d8dde0 0%,#9ea39f 35%,#6a675f 60%,#8a2a2a 75%,#6e6a65 100%)}
.hero svg{position:absolute;top:104px}
.h2{font-family:"PT Sans Narrow",sans-serif;font-weight:700}
.search-title{left:76px;top:350px;font-size:17px;color:#666;display:flex;align-items:center;gap:5px}
.search-panel{left:69px;top:375px;width:541px;height:110px;background:var(--panel);border-radius:3px}
.input{background:#fff;border:1px solid #ccc;font-size:6.5px;color:#aaa;font-style:italic;padding:0 4px;display:flex;align-items:center}
.btn-dark{background:linear-gradient(#6a6a6a,#333);color:#fff;font-size:7px;font-weight:700;display:flex;align-items:center;justify-content:center;border-radius:3px}
.map-icon{left:170px;top:421px;width:60px;height:58px;border-radius:9px;background:linear-gradient(#f0e6b8,#c9c08a)}
.select{background:#fff;border:1px solid #bbb;font-size:7px;color:#333;padding:0 4px;display:flex;align-items:center;justify-content:space-between;height:14px}
.select::after{content:"";border:4px solid transparent;border-top:5px solid #444;margin-top:4px}
.check{font-family:"PT Sans Narrow",sans-serif;font-weight:700;font-size:10px;color:#333;display:flex;align-items:center;gap:4px}
.check i{width:8px;height:8px;border:1px solid #888;background:#fff;display:block}
.sec-gold{color:var(--gold);font-size:13px}
.showcase{left:72px;top:529px;width:348px;height:172px;background:var(--cream);border:1px solid var(--cream-edge)}
.photo{background:linear-gradient(#6d8a4a,#3f5a2c 60%,#8c8a7a);border:4px solid #fff;box-shadow:0 1px 3px rgba(0,0,0,.4);transform:rotate(-4deg)}
.body-text{font-size:7px;line-height:10px;color:#6a5a20}
.script{font-family:"Great Vibes",cursive;font-size:14px;color:#2f5a1a}
.reg-title{left:74px;top:719px;font-size:13px;color:var(--red)}
.reg-panel{left:72px;top:740px;width:351px;height:203px;background:linear-gradient(#e9e9e9,#a7a7a7);border:1px solid #9a9a9a;border-radius:3px}
.label{font-size:7px;color:#222;font-style:italic}
.field{background:#fff;border:1px solid #bbb;height:15px}
.sub{font-family:"PT Sans Narrow",sans-serif;font-weight:700;font-size:11px;color:#222}
.submit{background:linear-gradient(#ea2a2a,#a91414);color:#fff;font-weight:700;font-size:7px;display:flex;align-items:center;justify-content:center;border-radius:3px}
.seen{left:88px;top:980px;font-family:"PT Sans Narrow",sans-serif;font-weight:700;font-size:13px;color:#999}
.press{font-family:"PT Sans Narrow",sans-serif;font-weight:700;font-size:12px;line-height:16px;color:#444;white-space:nowrap}
.press-serif{font-family:Georgia,"Times New Roman",serif;font-weight:400;font-size:11px}
.touch{left:444px;top:505px;font-size:15px;color:#2b4a7a}
.like{left:446px;top:530px;display:flex;gap:5px;font-size:6.5px;color:#444;line-height:8px}
.like-btn{width:30px;height:14px;border:1px solid #aab;background:#eef;font-size:6.5px;display:flex;align-items:center;justify-content:center;color:#2a3f6a}
.loop-box{left:445px;top:557px;width:164px;height:189px;border:1px solid #8fa3c8;background:#fff}
.loop-head{height:22px;background:var(--loop);color:#fff;display:flex;align-items:center;justify-content:space-between;padding:0 6px;font-size:7px}
.loop-head b{font-size:11px}
.item{display:flex;gap:6px;padding:0 4px;margin-top:8px}
.item i{width:20px;height:20px;background:var(--loop);display:block;flex:none;border-radius:2px}
.item p{font-size:6.5px;font-weight:700;color:var(--blue);line-height:9px}
.item small{display:block;color:#aaa;font-weight:400;font-size:6px}
.pill{background:var(--loop);color:#fff;font-size:6px;display:flex;align-items:center;justify-content:center;height:12px;border-radius:2px}
.news-title{left:445px;top:767px;font-size:13px;color:#555}
.news{left:445px;display:flex;gap:6px;width:165px;font-size:7px;line-height:10px;color:#333}
.news i{width:21px;height:21px;background:linear-gradient(#8a6a5a,#3a3030);display:block;flex:none}
.more{font-size:7px;color:var(--red)}
.blog-title{left:445px;top:906px;display:flex;align-items:center;gap:6px;font-size:13px;color:#d2691e}
.blog-icon{width:22px;height:22px;border-radius:50%;background:#e8731e}
.blog-p{left:448px;width:162px;font-size:7px;line-height:10.5px;color:var(--blue);padding-bottom:4px;border-bottom:1px solid #ddd}
.footer-h{left:72px;top:1093px;font-size:8px;font-weight:700;color:#777}
.footer-col{font-size:7px;line-height:14px;color:var(--footer-text)}
.copy{left:70px;top:1185px;font-size:7px;color:#ccc}
.line{left:62px;top:1177px;width:556px;height:1px;background:#333}
</style>
</head>
<body>
<div class="page">
  <div class="abs sheet"></div>

  <header class="abs header"></header>
  <div class="abs brand">
    <span class="brand-mark"></span>
    <div class="brand-name">LAKE VORISSA<br>REAL ESTATE</div>
  </div>
  <div class="abs join">Join Us on</div>
  <div class="abs social">
    <span style="background:#3b5998"></span><span style="background:#3aa0d8"></span><span style="background:#e8731e"></span><span style="background:#ddd"></span>
  </div>

  <nav class="abs nav">
    <a class="home" href="#"><svg width="10" height="9" viewBox="0 0 10 9"><path d="M5 0L0 4h1.5v5h2.5V6h2v3h2.5V4H10z" fill="#eee"/></svg></a>
    <a class="active" href="#">Company</a>
    <a href="#">Associates</a>
    <a href="#">Search Properties</a>
    <a href="#">Marketing &amp; Design</a>
    <a href="#">About Us</a>
    <a href="#">Developments</a>
    <a href="#">Contact Us</a>
  </nav>

  <div class="abs hero" role="img" aria-label="Photo of a bright luxury living room with white sofas and a red ottoman">
    <svg style="left:12px" width="14" height="20" viewBox="0 0 14 20"><path d="M11 2L3 10l8 8" stroke="#fff" stroke-width="4" fill="none"/></svg>
    <svg style="left:530px" width="14" height="20" viewBox="0 0 14 20"><path d="M3 2l8 8-8 8" stroke="#fff" stroke-width="4" fill="none"/></svg>
  </div>

  <div class="abs search-title h2">
    <svg width="18" height="18" viewBox="0 0 18 18"><circle cx="7" cy="7" r="5" fill="#cfe6f7" stroke="#5a9ad0" stroke-width="2"/><path d="M11 11l5 5" stroke="#c89a2a" stroke-width="3"/></svg>
    Search Property
  </div>
  <div class="abs search-panel"></div>
  <div class="abs input" style="left:79px;top:388px;width:156px;height:21px">MLS ID, Building Name, Add, City, ZipCode</div>
  <div class="abs btn-dark" style="left:79px;top:417px;width:46px;height:16px">SEARCH</div>
  <div class="abs h2" style="left:79px;top:463px;font-size:12px;color:#444">Easy Map Search</div>
  <div class="abs map-icon" role="img" aria-label="Map app icon with a location pin"></div>
  <div class="abs check" style="left:279px;top:381px"><i></i>For Sale</div>
  <div class="abs check" style="left:328px;top:381px"><i></i>For Rent</div>
  <div class="abs select" style="left:279px;top:398px;width:153px">City</div>
  <div class="abs select" style="left:439px;top:398px;width:154px">Area</div>
  <div class="abs select" style="left:279px;top:419px;width:153px">Property Type</div>
  <div class="abs select" style="left:439px;top:419px;width:154px">Price Range</div>
  <div class="abs select" style="left:279px;top:440px;width:102px">Beds</div>
  <div class="abs select" style="left:386px;top:440px;width:100px">Baths</div>
  <div class="abs select" style="left:491px;top:440px;width:102px">Square Feets</div>
  <div class="abs btn-dark" style="left:279px;top:460px;width:51px;height:16px;font-style:italic">SEARCH</div>
  <div class="abs" style="left:343px;top:464px;font-size:8px;color:#222">Click here for <span style="color:#2a7ac0">Advanced Search</span></div>

  <div class="abs h2 sec-gold" style="left:72px;top:508px">REAL ESTATE SHOWCASE</div>
  <section class="abs showcase">
    <div class="abs photo" role="img" aria-label="Photo of a college building among trees" style="left:12px;top:14px;width:92px;height:62px"></div>
    <p class="abs body-text" style="left:122px;top:13px;width:218px;text-align:justify">Lorem ipsum dolor sit amet, consectetur adipiscing elit. Morbi iaculis pretium leo, eu faucibus urna ultricies non. Phasellus at diam eget ligula pretium blandit vel et ante. Integer vestibulum congue nisl, congueNullam dictum dapibus felis, non tincidunt ipsum vulputate ut. Pellentesque eu fringilla ante. Proin ullamcorper mattis diam et consequat.</p>
    <div class="abs script" style="left:14px;top:87px">Professional Service . . . Proven Results</div>
    <div class="abs" style="left:314px;top:86px;font-size:7px;color:#555">...More</div>
    <div class="abs h2" style="left:12px;top:126px;font-size:13px;color:#2a4a8a;line-height:13px">BRIGHTMARK<br>REALTY</div>
    <div class="abs" style="left:114px;top:126px;font-size:7px;line-height:14px;color:#333">Brightmark Realty, LLC<br>info@brightmarkrealty.net &nbsp;|&nbsp; Phone: 555-201-4470<br>Fax: 555-201-4481 &nbsp;|&nbsp; Toll Free: 1-800-555-0142</div>
  </section>

  <div class="abs h2 reg-title">Registration</div>
  <section class="abs reg-panel">
    <div class="abs sub" style="left:8px;top:10px">Login Details</div>
    <div class="abs label" style="left:9px;top:35px">Username</div><div class="abs field" style="left:45px;top:32px;width:122px"></div>
    <div class="abs label" style="left:186px;top:35px">Email</div><div class="abs field" style="left:208px;top:32px;width:122px"></div>
    <div class="abs label" style="left:9px;top:57px">Password</div><div class="abs field" style="left:45px;top:54px;width:122px"></div>
    <div class="abs label" style="left:186px;top:57px">Confirm Password</div><div class="abs field" style="left:251px;top:54px;width:79px"></div>
    <div class="abs sub" style="left:8px;top:81px">User Details</div>
    <div class="abs label" style="left:9px;top:105px">Name</div><div class="abs field" style="left:45px;top:102px;width:122px"></div>
    <div class="abs label" style="left:186px;top:105px">Occupation</div><div class="abs select" style="left:229px;top:102px;width:102px;height:15px;font-style:italic;color:#999;font-size:6.5px">Select Occupation</div>
    <div class="abs label" style="left:9px;top:127px">Country</div><div class="abs field" style="left:45px;top:124px;width:122px"></div>
    <div class="abs label" style="left:9px;top:152px">Mobile</div>
    <div class="abs field" style="left:45px;top:147px;width:42px;font-size:6px;color:#aaa;font-style:italic;padding:3px 2px">CountryCode</div>
    <div class="abs field" style="left:87px;top:147px;width:80px"></div>
    <div class="abs label" style="left:190px;top:149px">Landline</div><div class="abs field" style="left:226px;top:145px;width:104px"></div>
    <div class="abs submit" style="left:45px;top:175px;width:52px;height:18px">SUBMIT</div>
  </section>

  <div class="abs seen">As seen on:</div>
  <div class="abs press" style="left:161px;top:981px;color:#c0202a">KTV</div>
  <div class="abs press press-serif" style="left:212px;top:981px;color:#222">The Daily Ledger</div>
  <div class="abs press" style="left:320px;top:981px;color:#b01e26">BNS</div>
  <div class="abs press" style="left:163px;top:1012px">NBT</div>
  <div class="abs press" style="left:212px;top:1012px;color:#c0202a">Weekview</div>
  <div class="abs press press-serif" style="left:294px;top:1012px;color:#2a6a9a;font-size:9px">THE MARKET JOURNAL</div>

  <div class="abs h2 touch">Stay In Touch</div>
  <div class="abs like"><span class="like-btn">Like</span><span><b style="color:#2a3f6a">22 people</b> like this. Be<br>the first of your friends.</span></div>
  <aside class="abs loop-box">
    <div class="loop-head"><span>Recent Activity</span><b>friendloop</b></div>
    <div class="item"><i></i><p>Lorem ipsum dolor sit amet, consectet ur adipiscing elit!<small>1,891 people shared this.</small></p></div>
    <div class="item"><i></i><p>Sed pharetra eros et nibh tempus aliqu et aliquam felis pulvinar.<small>1,866 people shared this.</small></p></div>
    <div class="item"><i></i><p>Aenean in turpis lorem, eget dignissim.<small>3,383 people shared this.</small></p></div>
    <div class="item"><i></i><p>Curabitur eget sapien quis turpis<small>752 people shared this.</small></p></div>
    <div class="abs pill" style="left:4px;top:173px;width:78px">Share on Friendloop</div>
    <div class="abs pill" style="left:120px;top:173px;width:38px">Login</div>
  </aside>

  <div class="abs h2 news-title">Latest News</div>
  <div class="abs news" style="top:790px"><i></i><span>Lorem ipsum dolor sit amet, consectur ectetur adipiscing elit.</span></div>
  <div class="abs news" style="top:821px"><i></i><span>Morbi iaculis pretium leo, eu faucibus urna ultricies non.</span></div>
  <div class="abs news" style="top:852px"><i></i><span>Vestibulum eget augue quam, nec tristique neque.</span></div>
  <div class="abs more" style="left:573px;top:877px">Read More</div>

  <div class="abs h2 blog-title"><span class="blog-icon"></span>Blog</div>
  <p class="abs blog-p" style="top:938px">Lorem ipsum dolor sit amet, consectetur adipiscing elit. Morbi iaculis pretium leo, eu faucibus urna ultricies non.</p>
  <p class="abs blog-p" style="top:980px">Phasellus at diam eget ligula pretium blandit vel et ante. Integer vestibulum congue nisl, congue</p>
  <p class="abs blog-p" style="top:1011px;border:0">Nullam dictum dapibus felis, non tincidunt ipsum vulputate ut. Pellentesque eu fringilla ante. Proin ullamcorper mattis diam et consequat.</p>
  <div class="abs more" style="left:573px;top:1049px;color:#d2691e">Read More</div>

  <footer>
    <div class="abs footer-h">Contact Us</div>
    <div class="abs footer-col" style="left:72px;top:1107px">Tom Aldane<br>Lot 4 Fernhill Road,<br>Brookvale, SA, 5199<br>PO Box 902,<br>Brookvale, SA, 5199</div>
    <div class="abs footer-col" style="left:159px;top:1107px">Phone Work/Mobile: 0400555123<br>Phone: 08 5550 1234<br>Fax: 08 55501299<br>Email: tom@fernhillfencing.example</div>
    <div class="abs line"></div>
    <div class="abs copy">© 2012 Lake Vorissa. All Rights Reserved.</div>
  </footer>
</div>
</body>
</html>
```